Business Card Design needed for start up company Halvora

In need of a new business card designed for a start up company based in Sydney, Halvora is a new start up innovative Company, our mission it to make property accessible for everyday Australian and to become the leading Real Estate platform in Australia. We want it to be fresh and clean.

Industry/Entity Type

Financial

Contact Information for Business Card

Section for Name
Section for Title

HALVORA - The Strength of Pooling
Mobile:
Direct:

Font styles to use
Sans Serif

Colors
33a6d7
0692cd
0255a3
ffffff

Requirements
Must have
• Logo, all business card details

```html
<!DOCTYPE html>
<html lang="en">
<head>
<meta charset="UTF-8">
<title>Halvora Business Card</title>
<link href="https://fonts.googleapis.com/css2?family=Montserrat:wght@600;800&family=Roboto:wght@400&display=swap" rel="stylesheet">
<style>
  :root {
    --sky: #5bc3ee;
    --sky-deep: #33a6d7;
    --navy: #0255a3;
    --white: #ffffff;
    --backdrop: #e6e6e6;
  }
  * { margin: 0; padding: 0; box-sizing: border-box; }
  html, body { width: 1200px; height: 900px; overflow: hidden; }
  body {
    background: var(--backdrop);
    position: relative;
    font-family: "Roboto", Arial, sans-serif;
  }
  .card {
    position: absolute;
    left: 300px;
    width: 600px;
    height: 343px;
    background: var(--white);
    border-radius: 28px;
    overflow: hidden;
    box-shadow: 0 6px 18px rgba(0,0,0,0.12);
  }
  .card--front { top: 90px; }
  .card--back { top: 467px; }

  .wordmark {
    position: absolute;
    display: flex;
    align-items: center;
    gap: 14px;
  }
  .wordmark__dot {
    flex: none;
    border-radius: 50%;
    background: var(--sky-deep);
  }
  .wordmark__name {
    font-family: "Montserrat", Arial, sans-serif;
    font-weight: 800;
    color: var(--navy);
    letter-spacing: 1px;
    white-space: nowrap;
  }
  .card--front .brand {
    position: absolute;
    left: 50%;
    top: 50%;
    transform: translate(-50%, -50%);
    display: flex;
    flex-direction: column;
    align-items: center;
    gap: 14px;
  }
  .card--front .wordmark { position: static; }
  .card--front .wordmark__dot { width: 86px; height: 86px; }
  .card--front .wordmark__name { font-size: 62px; }
  .tagline {
    font-family: "Montserrat", Arial, sans-serif;
    font-weight: 600;
    font-size: 13px;
    letter-spacing: 3px;
    color: var(--sky-deep);
    text-transform: uppercase;
    white-space: nowrap;
  }

  .card--back .wordmark { left: 40px; top: 150px; gap: 10px; }
  .card--back .wordmark__dot { width: 44px; height: 44px; }
  .card--back .wordmark__name { font-size: 28px; }

  .contact-panel {
    position: absolute;
    left: 292px;
    top: -117px;
    width: 474px;
    height: 474px;
    border-radius: 50%;
    background: linear-gradient(135deg, var(--sky) 0%, #4bb8ea 100%);
  }
  .contact {
    position: absolute;
    left: 352px;
    top: 104px;
  }
  .contact__name {
    font-family: "Montserrat", Arial, sans-serif;
    font-weight: 800;
    font-size: 24px;
    color: var(--navy);
    letter-spacing: 1.5px;
    white-space: nowrap;
  }
  .contact__title {
    font-size: 12px;
    letter-spacing: 2px;
    text-transform: uppercase;
    color: var(--white);
    margin: 2px 0 10px;
  }
  .contact__row {
    display: flex;
    align-items: center;
    gap: 10px;
    color: var(--white);
    font-size: 13px;
    letter-spacing: 0.8px;
    line-height: 22px;
    white-space: nowrap;
  }
  .contact__label { color: var(--navy); }
  .contact__icon { width: 13px; height: 13px; flex: none; }
</style>
</head>
<body>
  <section class="card card--front">
    <div class="brand">
      <div class="wordmark">
        <span class="wordmark__dot"></span>
        <span class="wordmark__name">HALVORA</span>
      </div>
      <p class="tagline">The Strength of Pooling</p>
    </div>
  </section>

  <section class="card card--back">
    <div class="wordmark">
      <span class="wordmark__dot"></span>
      <span class="wordmark__name">HALVORA</span>
    </div>
    <div class="contact-panel"></div>
    <div class="contact">
      <p class="contact__name">MARA LIND</p>
      <p class="contact__title">Co-Founder</p>
      <p class="contact__row">
        <svg class="contact__icon" viewBox="0 0 16 16" aria-hidden="true"><path fill="#0255a3" d="M3.5 1.5l2.5 3-1.5 1.5c.8 2 2.5 3.7 4.5 4.5l1.5-1.5 3 2.5-1.5 2.5C7 13.5 2.5 9 1 3z"/></svg>
        <span><span class="contact__label">M</span> 02 5550 1847</span>
      </p>
      <p class="contact__row">
        <svg class="contact__icon" viewBox="0 0 16 16" aria-hidden="true"><path fill="#0255a3" d="M3.5 1.5l2.5 3-1.5 1.5c.8 2 2.5 3.7 4.5 4.5l1.5-1.5 3 2.5-1.5 2.5C7 13.5 2.5 9 1 3z"/></svg>
        <span><span class="contact__label">D</span> +61 455 503 291</span>
      </p>
      <p class="contact__row">
        <svg class="contact__icon" viewBox="0 0 16 16" aria-hidden="true"><rect x="1.5" y="3.5" width="13" height="9" fill="none" stroke="#0255a3" stroke-width="1.5"/><path d="M1.5 3.5L8 9l6.5-5.5" fill="none" stroke="#0255a3" stroke-width="1.5"/></svg>
        <span>mara@halvora-mail.com</span>
      </p>
    </div>
  </section>
</body>
</html>
```